TALMORK

The business want a professional looking business card. We have a scetch we will add but want the extra upgrade, and would like more suggestions for variations of our business cards.

```html
<!DOCTYPE html>
<html lang="en">
<head>
<meta charset="utf-8">
<title>TALMORK business cards</title>
<link href="https://fonts.googleapis.com/css2?family=Figtree:wght@400;500&display=swap" rel="stylesheet">
<style>
  :root {
    --backdrop: #cbcac6;
    --card-light: #f8f5ea;
    --card-warm: #ece2c8;
    --ink-brown: #5a4120;
    --gold: #b8914a;
  }
  * { margin: 0; padding: 0; box-sizing: border-box; }
  html, body { width: 1200px; height: 805px; overflow: hidden; }
  body {
    position: relative;
    background: var(--backdrop);
    font-family: "Figtree", sans-serif;
    color: var(--ink-brown);
  }
  .card {
    position: absolute;
    width: 487px;
    height: 296px;
    background: linear-gradient(125deg, var(--card-light) 0%, #f4eedc 55%, var(--card-warm) 100%);
    box-shadow: 0 2px 6px rgba(0,0,0,0.18);
  }
  .card--contact { left: 95px; top: 87px; }
  .card--brand { left: 617px; top: 87px; }
  .card--since { left: 359px; top: 421px; width: 481px; height: 304px;
    background: linear-gradient(90deg, var(--card-light) 0%, #f3ecd9 60%, var(--card-warm) 100%); }

  .contact-name { position: absolute; left: 48px; top: 50px; font-size: 34px; font-weight: 400; }
  .contact-role { position: absolute; left: 48px; top: 101px; font-size: 22px; font-weight: 400; }
  .contact-list { position: absolute; left: 48px; top: 178px; list-style: none; }
  .contact-list li { display: flex; align-items: center; height: 33px; font-size: 20px; }
  .contact-list svg { width: 22px; height: 22px; margin-right: 14px; fill: var(--ink-brown); }

  .brand-lockup {
    position: absolute; left: 0; right: 0;
    display: flex; flex-direction: column; align-items: center;
  }
  .card--brand .brand-lockup { top: 78px; }
  .card--since .brand-lockup { top: 62px; }
  .brand-dot { width: 64px; height: 64px; border-radius: 50%; background: var(--gold); margin-bottom: 28px; }
  .card--since .brand-dot { background: var(--ink-brown); }
  .brand-name { font-size: 40px; font-weight: 500; letter-spacing: 7px; padding-left: 7px; color: var(--ink-brown); }
  .card--since .brand-name { font-size: 46px; }
  .brand-since { margin-top: 16px; font-size: 15px; letter-spacing: 5px; padding-left: 5px; }
</style>
</head>
<body>
  <section class="card card--contact">
    <h1 class="contact-name">Aksel Brenna Solvik</h1>
    <p class="contact-role">CEO &amp; Founder</p>
    <ul class="contact-list">
      <li><svg viewBox="0 0 24 24" aria-hidden="true"><path d="M7 1h10a2 2 0 0 1 2 2v18a2 2 0 0 1-2 2H7a2 2 0 0 1-2-2V3a2 2 0 0 1 2-2zm0 3v14h10V4zm5 15.5a1.2 1.2 0 1 0 0 2.4 1.2 1.2 0 0 0 0-2.4z"/></svg>004791234567</li>
      <li><svg viewBox="0 0 24 24" aria-hidden="true"><path d="M2 5h20v14H2zm2 2v.4l8 5.4 8-5.4V7zm0 2.8V17h16V9.8l-8 5.4z"/></svg>post@talmork.llc</li>
      <li><svg viewBox="0 0 24 24" aria-hidden="true"><path d="M12 2a10 10 0 1 0 0 20 10 10 0 0 0 0-20zm6.9 9h-3a15 15 0 0 0-1.3-6.1A8 8 0 0 1 18.9 11zM12 4.1c.9 1.3 1.8 3.7 1.9 6.9h-3.8c.1-3.2 1-5.6 1.9-6.9zM9.4 4.9A15 15 0 0 0 8.1 11h-3a8 8 0 0 1 4.3-6.1zM5.1 13h3a15 15 0 0 0 1.3 6.1A8 8 0 0 1 5.1 13zm6.9 6.9c-.9-1.3-1.8-3.7-1.9-6.9h3.8c-.1 3.2-1 5.6-1.9 6.9zm2.6-.8a15 15 0 0 0 1.3-6.1h3a8 8 0 0 1-4.3 6.1z"/></svg>www.talmork.llc</li>
    </ul>
  </section>

  <section class="card card--brand">
    <div class="brand-lockup">
      <span class="brand-dot" aria-hidden="true"></span>
      <p class="brand-name">TALMORK</p>
    </div>
  </section>

  <section class="card card--since">
    <div class="brand-lockup">
      <span class="brand-dot" aria-hidden="true"></span>
      <p class="brand-name">TALMORK</p>
      <p class="brand-since">SINCE 2026</p>
    </div>
  </section>
</body>
</html>
```